Business card for my new company (Accounting firm)

I need a business card for my new business Brightwell Advisory and Ledger SA. Our services are accounting, tax, audit and financial management. Our customers are small companies, start-ups and new companies. The final design has to show financial security, trust and growth. Please find our logo attached to the business card. Text for the business card: Brightwell Advisory and Ledger SA Tomas Varenholt Director and Founder Certified Accountant Tel. 022 418 57 34 tv@clairevalconseil.ch www.clairevalconseil.ch Rue des Vergières 27 1201 Geneva
Target Market(s)
Our customers are small companies, start-ups and new companies.
Industry/Entity Type
Finance And Accounting
Contact Information for Business Card
Claireval Conseil et Comptes SA
Tomas Varenholt
Directeur et Fondateur
Expert-comptable diplômé
Tél. 022 418 57 34
tv@clairevalconseil.ch
www.clairevalconseil.ch
Rue des Vergières 27
1201 Genève

```html
<!DOCTYPE html>
<html lang="fr">
<head>
<meta charset="utf-8">
<title>Claireval Conseil et Comptes – Business Card</title>
<link href="https://fonts.googleapis.com/css2?family=Lato:wght@400;700&display=swap" rel="stylesheet">
<style>
  :root {
    --stage: #b9b9b9;
    --ink-dark: #3c3c3e;
    --blue-top: #1f8fd3;
    --blue-mid: #2fb0e4;
    --blue-low: #1a6fae;
    --blue-mark: #2a9fdc;
    --white: #ffffff;
  }
  * { margin: 0; padding: 0; box-sizing: border-box; }
  html, body {
    width: 1200px; height: 802px; overflow: hidden;
    background: var(--stage);
    font-family: "Lato", sans-serif;
  }
  .stage { position: relative; width: 1200px; height: 802px; }
  .card {
    position: absolute; top: 274px; width: 443px; height: 264px;
    overflow: hidden;
    box-shadow: 0 3px 6px rgba(0,0,0,0.35);
  }
  .card--front {
    left: 136px;
    background: linear-gradient(180deg, var(--blue-top) 0%, var(--blue-mid) 45%, var(--blue-mid) 70%, var(--blue-low) 100%);
  }
  .card--back { left: 624px; background: var(--ink-dark); }

  .front__panel {
    position: absolute; inset: 0;
    background: var(--ink-dark);
    clip-path: polygon(295px 0, 443px 0, 443px 264px, 149px 264px);
  }
  .front__info { position: absolute; left: 22px; top: 0; color: var(--white); }
  .front__name {
    position: absolute; top: 33px; white-space: nowrap;
    font-weight: 700; font-size: 14.5px; letter-spacing: -0.2px;
  }
  .front__role { position: absolute; top: 52px; font-size: 12px; line-height: 15.5px; white-space: nowrap; }
  .contact { position: absolute; top: 105px; list-style: none; font-size: 12px; }
  .contact li { display: flex; align-items: center; height: 16.3px; white-space: nowrap; }
  .contact svg { width: 10px; height: 10px; margin-right: 11px; fill: var(--white); }
  .front__address { position: absolute; top: 171px; font-size: 12px; line-height: 16px; font-style: normal; white-space: nowrap; }

  .back__brand {
    position: absolute; left: 0; right: 0; top: 60px;
    display: flex; flex-direction: column; align-items: center;
    color: var(--white); font-weight: 400;
  }
  .back__dot { width: 46px; height: 46px; border-radius: 50%; background: var(--blue-mark); margin-bottom: 22px; }
  .back__name { font-size: 29px; letter-spacing: 2px; line-height: 1; }
  .back__tagline { font-size: 10px; letter-spacing: 1.6px; margin-top: 5px; }
</style>
</head>
<body>
<main class="stage">
  <section class="card card--front" aria-label="Card front">
    <div class="front__panel"></div>
    <div class="front__info">
      <h1 class="front__name">SA TOMAS VARENHOLT</h1>
      <p class="front__role">Director and Founder<br>Certified Accountant</p>
      <ul class="contact">
        <li><svg viewBox="0 0 10 10"><path d="M1 3.2C1 2 2.5 1.2 5 1.2S9 2 9 3.2V4H7V3H3v1H1zM2.5 5h5L9 9H1z"/></svg>022 418 57 34</li>
        <li><svg viewBox="0 0 10 10"><path d="M0.5 2h9v6h-9zM1.3 2.6L5 5.6l3.7-3V3.3L5 6.3 1.3 3.3z" fill-rule="evenodd"/></svg>tv@clairevalconseil.ch</li>
        <li><svg viewBox="0 0 10 10"><circle cx="5" cy="5" r="4.5"/><path d="M3 3.5l2-1 1 1.5-1.5 1 .5 2-1.5.5L3 5.5z" fill="#2fb0e4"/></svg>www.clairevalconseil.ch</li>
      </ul>
      <address class="front__address">Rue des Vergières 27<br>1201 Geneva</address>
    </div>
  </section>

  <section class="card card--back" aria-label="Card back">
    <div class="back__brand">
      <span class="back__dot"></span>
      <span class="back__name">CLAIREVAL</span>
      <span class="back__tagline">CONSEIL ET COMPTES</span>
    </div>
  </section>
</main>
</body>
</html>
```